RTavenor Business Cards & Letterhead

I have a logo but need a design for some new business cards. We are a Design-Build Firm that specializes in the design and construction of commercial projects.
the cards need to be professional. no cartoon stuff.
i would like to have the cards in AI format so I can update the card as needed. Logo is provided.
Our Address is: 4187 Marlowe Ct. Larkmoor, Southern Vale 27614

```html
<!DOCTYPE html>
<html lang="en">
<head>
<meta charset="utf-8">
<title>RTavenor Business Card</title>
<link rel="stylesheet" href="https://fonts.googleapis.com/css2?family=Lexend:wght@600;700&family=Mulish:wght@400;500&display=swap">
<style>
  :root {
    --page-bg: #e4e4e3;
    --brand-blue: #14578c;
    --brand-blue-light: #1a7ab4;
    --brand-blue-dark: #0f4a78;
    --ink-grey: #4a4a4c;
    --text-grey: #3d3d3f;
    --rule-grey: #555557;
    --card-white: #f4f4f4;
  }
  * { margin: 0; padding: 0; box-sizing: border-box; }
  html, body {
    width: 1200px;
    height: 1200px;
    overflow: hidden;
    background: var(--page-bg);
  }
  .canvas {
    position: relative;
    width: 1200px;
    height: 1200px;
  }
  .card {
    position: absolute;
    left: 234px;
    width: 731px;
    height: 418px;
  }
  .card-front {
    top: 160px;
    background: linear-gradient(115deg, var(--brand-blue-dark) 0%, var(--brand-blue) 45%, var(--brand-blue-light) 100%);
  }
  .card-back {
    top: 632px;
    background: var(--card-white);
    font-family: "Mulish", sans-serif;
    color: var(--text-grey);
  }
  .brand {
    position: absolute;
    right: 68px;
    top: 70px;
    display: flex;
    align-items: center;
    gap: 12px;
  }
  .brand-square {
    width: 24px;
    height: 24px;
    background: var(--brand-blue);
  }
  .brand-name {
    font-family: "Lexend", sans-serif;
    font-weight: 600;
    font-size: 37px;
    letter-spacing: 0.5px;
    color: var(--ink-grey);
    line-height: 1;
  }
  .holder {
    position: absolute;
    left: 67px;
    top: 164px;
  }
  .holder-name {
    font-family: "Lexend", sans-serif;
    font-weight: 700;
    font-size: 32px;
    color: var(--brand-blue);
    line-height: 1.1;
  }
  .holder-title {
    font-size: 20px;
    margin-top: 3px;
  }
  .divider {
    position: absolute;
    left: 67px;
    right: 68px;
    top: 243px;
    height: 2px;
    background: var(--rule-grey);
  }
  .contacts {
    position: absolute;
    left: 67px;
    top: 263px;
    list-style: none;
    font-size: 20.5px;
    line-height: 27.5px;
  }
  .contacts li {
    display: flex;
    align-items: center;
    gap: 10px;
  }
  .contacts svg {
    width: 16px;
    height: 16px;
    fill: var(--brand-blue);
  }
  .address {
    position: absolute;
    right: 68px;
    top: 293px;
    text-align: right;
    font-size: 20.5px;
    line-height: 27px;
    font-style: normal;
  }
</style>
</head>
<body>
<div class="canvas">
  <div class="card card-front" role="img" aria-label="Repeating brand symbol pattern on a blue field"></div>

  <div class="card card-back">
    <div class="brand">
      <span class="brand-square"></span>
      <span class="brand-name">RTAVENOR</span>
    </div>

    <div class="holder">
      <div class="holder-name">Rowan Tavenor</div>
      <div class="holder-title">President</div>
    </div>

    <div class="divider"></div>

    <ul class="contacts">
      <li>
        <svg viewBox="0 0 16 16" aria-hidden="true"><path d="M3.5 1.5l2.6 2.7-1.4 1.9c.9 2 2.4 3.5 4.4 4.4l1.9-1.4 2.7 2.6-1.8 2.3C6.9 13.7 2.3 9.1 1.3 3.1z"/></svg>
        <span>(919)-555-0142</span>
      </li>
      <li>
        <svg viewBox="0 0 16 16" aria-hidden="true"><path d="M1 3h14v10H1z"/><path d="M2 3.5L8 8l6-4.5" stroke="#f4f4f4" stroke-width="1.3" fill="none"/></svg>
        <span>info@rtavenor.com</span>
      </li>
      <li>
        <svg viewBox="0 0 16 16" aria-hidden="true"><circle cx="8" cy="8" r="7"/><path d="M1 8h14M8 1c-3 3.5-3 10.5 0 14M8 1c3 3.5 3 10.5 0 14" stroke="#f4f4f4" stroke-width="1.1" fill="none"/></svg>
        <span>www.rtavenor.com</span>
      </li>
    </ul>

    <address class="address">
      4187 Marlowe Ct. Larkmoor,<br>
      Southern Vale 27614
    </address>
  </div>
</div>
</body>
</html>
```